Thornvale Group needs a business card design

We need a new business card design using the logo recently selected in a logo competition on Pixel Bazaar. Our business is a consultancy specializing in aviation and energy and the winning business card design will promote an image of precision and professionalism with creativity.

Please use the logo with the name on the front of the card and use a complementary font. Make the back white with either the light grey or dark grey logo.

Target Market(s)

Senior finance and legal leaders at aviation and energy companies

Industry/Entity Type

Management Consulting

Contact Information for Business Card

Peter Castrell
President
Thornvale Group

www.thornvalegroup.example

(555) 204-6391
pc@thornvalegroup.example

Requirements
Must have
• Professional font that goes well with the logo font

```html
<!DOCTYPE html>
<html lang="en">
<head>
<meta charset="utf-8">
<title>Thornvale Group — Business Card</title>
<link rel="stylesheet" href="https://fonts.googleapis.com/css2?family=Open+Sans:wght@400;600;700&display=swap">
<style>
  :root {
    --navy: #143f70;
    --white: #ffffff;
    --rule-grey: #6b6e72;
    --backdrop: #e4e5e6;
    --card-shadow: rgba(0, 0, 0, 0.18);
  }
  * { box-sizing: border-box; margin: 0; padding: 0; }
  html, body {
    width: 1200px;
    height: 900px;
    overflow: hidden;
    background: var(--backdrop);
    font-family: "Open Sans", Arial, sans-serif;
  }
  .sheet {
    position: relative;
    width: 1200px;
    height: 900px;
  }
  .card {
    position: absolute;
    left: 300px;
    width: 600px;
    height: 343px;
    overflow: hidden;
    box-shadow: 0 6px 18px var(--card-shadow);
  }
  .card--front { top: 80px; background: var(--navy); color: var(--white); }
  .card--back { top: 477px; background: var(--navy); color: var(--white); }

  /* Front */
  .front-content {
    position: absolute;
    inset: 0;
    display: flex;
    flex-direction: column;
    align-items: center;
    justify-content: center;
    text-align: center;
  }
  .brand-name {
    font-size: 34px;
    font-weight: 400;
    letter-spacing: 6px;
    text-transform: uppercase;
    line-height: 1.25;
    margin-bottom: 22px;
  }
  .tagline {
    font-size: 17px;
    font-weight: 700;
    margin-bottom: 4px;
  }
  .sectors {
    font-size: 16px;
    font-weight: 400;
  }

  /* Back */
  .back-panel {
    position: absolute;
    inset: 0;
  }
  .back-brand {
    position: absolute;
    left: 36px;
    top: 122px;
    width: 240px;
    color: var(--navy);
    font-size: 27px;
    font-weight: 400;
    letter-spacing: 5px;
    text-transform: uppercase;
    line-height: 1.3;
    text-align: center;
  }
  .contact {
    position: absolute;
    right: 40px;
    top: 102px;
    text-align: right;
  }
  .contact-name { font-size: 21px; font-weight: 700; letter-spacing: 0.5px; }
  .contact-title { font-size: 16px; font-weight: 400; margin-bottom: 22px; }
  .contact-line {
    display: flex;
    justify-content: flex-end;
    align-items: center;
    gap: 8px;
    font-size: 16px;
    line-height: 1.45;
  }
  .contact-icon { width: 14px; height: 14px; flex: none; }
</style>
</head>
<body>
<main class="sheet">

  <section class="card card--front" aria-label="Card front">
    <div class="front-content">
      <div class="brand-name">Thornvale<br>Group</div>
      <p class="tagline">Finance and Strategy Consulting</p>
      <p class="sectors">Aviation - Manufacturing - Energy</p>
    </div>
  </section>

  <section class="card card--back" aria-label="Card back">
    <svg class="back-panel" viewBox="0 0 600 343" preserveAspectRatio="none" aria-hidden="true">
      <polygon points="0,0 222,0 322,188 120,343 0,343" fill="#ffffff"/>
      <polyline points="226,0 328,190 126,343" fill="none" stroke="#6b6e72" stroke-width="4"/>
    </svg>
    <div class="back-brand">Thornvale<br>Group</div>
    <div class="contact">
      <p class="contact-name">Peter Castrell</p>
      <p class="contact-title">President</p>
      <p class="contact-line">(555) 204-6391
        <svg class="contact-icon" viewBox="0 0 24 24" aria-hidden="true"><path fill="#ffffff" d="M6.6 10.8a15.1 15.1 0 0 0 6.6 6.6l2.2-2.2a1 1 0 0 1 1-.25 11.4 11.4 0 0 0 3.6.57 1 1 0 0 1 1 1V20a1 1 0 0 1-1 1A17 17 0 0 1 3 4a1 1 0 0 1 1-1h3.5a1 1 0 0 1 1 1c0 1.25.2 2.45.57 3.57a1 1 0 0 1-.25 1z"/></svg>
      </p>
      <p class="contact-line">pc@thornvalegroup.example
        <svg class="contact-icon" viewBox="0 0 24 24" aria-hidden="true"><rect x="2" y="5" width="20" height="14" fill="#ffffff"/><path d="M2 5l10 8 10-8" fill="none" stroke="#143f70" stroke-width="1.8"/></svg>
      </p>
    </div>
  </section>

</main>
</body>
</html>
```